Digital Marketing Website Redesign, modern, fresh, dynamic

Hi there, we would like to freshen up our website and create a new dynamic look. We are a digital marketing agency who specialise in digital transformation in the form of creating websites for appointment bookings. Our clients are service businesses such as hairdressers, dentists and doctors who's patients need to book appointments with them.

Our company name is Tallomex with the point being we can help increase your revenue curve by increasing your appointment bookings.

Our services include building the website, creating campaigns to drive traffic, increasing conversions and monitoring and reporting.

We are playing with a tagline of 'Step into your Digital Transformation' as we have a 5 step journey that customers can take with us getting them from zero to full appointment bookings.

Our current website is www.tallomex-sample.com

You can see a draft design that I mocked up on Canva here https://www.draftboard-sample.com/design/QXB82LmpR7T/KpoW39dnFsYbZet_wqe_OPa/edit?utm_content=QXB82LmpR7T&utm_campaign=designshare&utm_medium=link2&utm_source=sharebutton

Also attached some other homepage ideas. In regard to photos we are open to ideas.

Please let if you need any more information to provide us with an initial design. Thanks million and I look forward to receiving fantastic designs :)

Marian Dobbs
Tallomex

Target Market(s)

Appointment based businesses such as hairdressers, dentists, doctors

Industry/Entity Type

Marketing and Digital

Coding

Coded - Design and coding required

Number of Pages Required

1 page

Colors
0094D4
00A9DD
6FCCEA
C7EBF8
E9F6FB

Requirements
Must have
• Appointment booking CTA
Nice to have
• A website we like https://www.fergalwhitty-sample.ie

```html
<!DOCTYPE html>
<html lang="en">
<head>
<meta charset="utf-8">
<title>Tallomex – Digital Marketing</title>
<link href="https://fonts.googleapis.com/css2?family=Open+Sans:wght@400;600;700&family=Arimo:wght@400;700&display=swap" rel="stylesheet">
<style>
:root{
  --navy:#23467b;
  --navy-deep:#0f2244;
  --lime:#c6d500;
  --page:#f4f4f4;
  --white:#ffffff;
  --text:#3a3a3a;
  --muted:#8a8a8a;
  --footer:#21262d;
  --orange:#f0592a;
}
*{margin:0;padding:0;box-sizing:border-box}
html,body{width:1200px;height:4615px;overflow:hidden}
body{position:relative;background:var(--page);font-family:"Arimo",Arial,sans-serif;color:var(--text)}
.abs{position:absolute}
h1,h2,h3,h4,.brand{font-family:"Open Sans",Arial,sans-serif}

/* header */
.site-header{left:0;top:0;width:1200px;height:82px;background:var(--white)}
.brand{font-weight:700;font-size:28px;color:var(--navy);letter-spacing:-.5px}
.site-header .brand{left:112px;top:24px}
.nav{left:402px;top:50px;display:flex;gap:0}
.nav a{font-size:11px;color:#444;text-decoration:none;width:100px}
.nav a.active{font-weight:700;color:var(--navy)}
.book-btn{left:842px;top:0;width:112px;height:24px;background:#77808d;color:#fff;font-size:8px;font-weight:700;text-align:center;line-height:24px;text-transform:uppercase}

/* hero */
.hero-bg{left:0;top:82px}
.hero-kicker{left:110px;top:268px;color:#fff;font-size:12px;letter-spacing:.5px;display:flex;align-items:center;gap:16px}
.hero-kicker span{display:block;width:44px;height:1px;background:#fff}
.hero-title{left:110px;top:322px;color:#fff;font-size:44px;line-height:56px;font-weight:600}
.hero-text{left:110px;top:476px;width:410px;color:#fff;font-size:12.5px;line-height:22px}
.btn{display:block;background:var(--lime);color:#fff;font-family:"Open Sans",Arial,sans-serif;font-weight:700;font-size:13px;text-align:center;border-radius:3px}
.hero-btn{left:110px;top:557px;width:169px;height:43px;line-height:43px}

/* section titles */
.sec-title{left:0;width:1200px;text-align:center;color:var(--navy);font-size:30px;font-weight:600}
.sec-text{width:540px;text-align:center;color:var(--muted);font-size:12.5px;line-height:22px}

/* why cards */
.why-card{top:969px;width:234px;height:217px;background:var(--white);box-shadow:0 2px 8px rgba(0,0,0,.12);text-align:center;padding-top:34px}
.why-card.featured{background:var(--navy)}
.why-card h3{font-size:18px;line-height:25px;color:var(--navy);font-weight:600;margin-top:16px}
.why-card.featured h3{color:#fff}
.why-card p{font-size:12.5px;line-height:22px;color:var(--muted);margin-top:6px}
.why-card.featured p{color:#fff}
.why-card svg{display:block;margin:0 auto}

/* vision */
.vision-band{left:281px;top:1320px;width:919px;height:469px;background:var(--navy)}
.vision-photo{left:0;top:1386px;width:582px;height:446px;background:linear-gradient(135deg,#e9e6e0,#c9bfb0 55%,#8f7d6a)}
.vision-title{left:632px;top:1408px;color:#fff;font-size:30px;font-weight:600}
.vision-text{left:632px;width:440px;color:#fff;font-size:12.5px;line-height:21.5px}
.vision-btn{left:632px;top:1651px;width:154px;height:43px;line-height:43px;display:flex;justify-content:center;align-items:center;gap:10px}

/* services */
.svc-photo{top:2061px;width:321px;height:237px}
.svc-card{top:2239px;width:285px;height:200px;background:var(--white);box-shadow:0 2px 8px rgba(0,0,0,.1);padding:26px 40px 0 40px}
.svc-card.featured{background:var(--navy)}
.svc-card h3{font-size:21px;color:var(--navy);font-weight:600;text-align:center;margin-left:-20px;margin-right:-20px}
.svc-card.featured h3{color:#fff}
.svc-card p{font-size:12.5px;line-height:21.5px;color:var(--muted);margin-top:10px}
.svc-card.featured p{color:#fff}
.svc-card .more{display:block;font-size:10.5px;font-weight:700;color:var(--lime);margin-top:12px}
.svc-card.featured .more{color:#fff}

/* cta band */
.cta-band{left:0;top:2511px;width:1200px;height:294px;background:radial-gradient(ellipse at 20% 60%,#1d4d7a 0,#0f2552 45%,#0a1a40 100%)}
.cta-phone{left:0;top:2562px;width:1200px;text-align:center;color:#fff;font-family:"Open Sans",Arial,sans-serif;font-size:22px;font-weight:600}
.cta-title{left:0;top:2600px;width:1200px;text-align:center;color:#fff;font-size:30px;font-weight:600}
.cta-btn{left:519px;top:2719px;width:167px;height:45px;border:1.5px solid #fff;border-radius:4px;color:#fff;font-weight:700;font-size:13px;text-align:center;line-height:42px;font-family:"Open Sans",Arial,sans-serif}

/* reviews */
.review{top:3014px;width:494px;height:255px;background:#ececec}
.review .rule{position:absolute;left:63px;top:43px;width:1px;height:172px;background:#bfbfbf}
.review .quote{position:absolute;left:40px;top:105px;width:46px;height:46px;border-radius:50%;background:var(--lime);border:3px solid #fff;box-shadow:0 0 0 1px #d6d6d6;color:#fff;font-family:"Open Sans",Arial,sans-serif;font-weight:700;font-size:30px;text-align:center;line-height:52px}
.review .stars{position:absolute;left:114px;top:38px;color:var(--orange);font-size:18px;letter-spacing:4px}
.review p{position:absolute;left:114px;top:84px;width:340px;font-size:12.5px;line-height:22px;color:var(--muted)}
.review h4{position:absolute;left:114px;top:174px;font-size:17px;font-weight:600;color:#222}
.review .place{position:absolute;left:114px;top:204px;font-size:12px;color:#555}
.review .avatar{position:absolute;left:398px;top:166px;width:58px;height:58px;border-radius:50%}
.dots{left:564px;top:3313px;display:flex;gap:9px}
.dots span{width:10px;height:10px;border-radius:50%;background:var(--orange)}
.dots span.off{background:none;border:1.5px solid var(--orange)}

/* contact */
.contact-box{left:90px;top:3568px;width:1017px;height:460px;background:var(--white);box-shadow:0 2px 10px rgba(0,0,0,.12)}
.contact-panel{left:90px;top:3568px;width:510px;height:460px;background:linear-gradient(135deg,#2e5a91 0,#365f8f 50%,#4a6c8c 100%)}
.contact-info{left:176px;top:3630px;color:#fff}
.contact-info .label{font-family:"Open Sans",Arial,sans-serif;font-weight:700;font-size:16px}
.contact-info .call{font-family:"Open Sans",Arial,sans-serif;font-weight:700;font-size:20px;margin-top:28px}
.contact-info .small{font-size:12px;font-weight:700;line-height:20px}
.socials{left:178px;top:3938px;display:flex;gap:10px}
.socials span{width:32px;height:32px;border-radius:50%;background:rgba(255,255,255,.35)}
.socials span.on{background:#fff}
.form-title{left:688px;top:3624px;color:var(--navy);font-family:"Open Sans",Arial,sans-serif;font-weight:700;font-size:16px}
.field{left:688px;width:332px;background:#f6f6f6;border:1px solid #ececec;font-size:9px;color:#666;padding:10px 14px}
.submit{left:688px;top:3942px;width:110px;height:36px;line-height:36px;font-size:11px}

/* info strip & footer */
.footer{left:0;top:4159px;width:1200px;height:456px;background:var(--footer)}
.info-strip{left:66px;top:4112px;width:1069px;height:104px;background:var(--lime);border-radius:4px}
.info-item{top:4130px;display:flex;gap:18px;align-items:center;color:#fff}
.info-item h4{font-size:17px;font-weight:600}
.info-item p{font-size:12.5px;font-weight:700;margin-top:10px}
.divider{top:4112px;width:28px;height:104px}
.foot-head{top:4288px;color:#fff;font-family:"Open Sans",Arial,sans-serif;font-weight:700;font-size:17px}
.foot-text{color:#fff;font-size:12.5px;line-height:31px}
.foot-links a{display:block;color:#fff;font-size:12.5px;text-decoration:underline;line-height:34px}
.read-more{color:#3f8fe0;font-size:15px;text-decoration:underline}
.subscribe{left:797px;top:4436px;width:339px;height:55px;background:#fff;border-radius:3px}
.subscribe .ph{position:absolute;left:16px;top:19px;font-size:13px;color:#666}
.subscribe .go{position:absolute;right:0;top:0;width:64px;height:55px;background:var(--lime);border-radius:0 3px 3px 0}
.foot-line{left:0;top:4549px;width:1200px;height:1px;background:#3a4049}
.foot-logo{left:66px;top:4549px;width:172px;height:66px;background:var(--lime)}
.foot-logo .brand{position:absolute;left:40px;top:18px;color:var(--navy);font-size:22px}
.foot-social{top:4549px;width:60px;height:66px;border-left:1px solid #3a4049}
.foot-social span{position:absolute;left:23px;top:26px;width:14px;height:14px;border-radius:50%;background:#59606b}
</style>
</head>
<body>

<header class="site-header abs">
  <div class="brand abs">Tallomex</div>
  <nav class="nav abs">
    <a class="active">Home</a><a>About Us</a><a>Services</a><a>Our Team</a><a>Projects</a><a>Contact Us</a>
  </nav>
  <div class="book-btn abs">Book Appointment</div>
</header>

<svg class="hero-bg abs" width="1200" height="760" viewBox="0 0 1200 760" role="img" aria-label="Person walking into a glowing digital tunnel">
  <defs>
    <radialGradient id="heroGlow" cx="0.55" cy="0.45" r="0.7">
      <stop offset="0" stop-color="#3f7fa8"/>
      <stop offset="0.35" stop-color="#1d3e5d"/>
      <stop offset="1" stop-color="#0a1628"/>
    </radialGradient>
  </defs>
  <path d="M0 0H1200V640C1050 760 820 710 620 690 380 665 200 600 0 640Z" fill="url(#heroGlow)"/>
  <path d="M430 625C620 690 860 760 1200 640V675C880 800 640 745 430 625Z" fill="var(--lime)"/>
  <path d="M540 650C700 710 900 745 1200 655V665C900 760 700 725 540 650Z" fill="var(--navy)"/>
  <path d="M0 640C200 600 380 665 620 690 820 710 1050 760 1200 640V760H0Z" fill="var(--page)"/>
</svg>
<div class="hero-kicker abs">DIGITAL MARKETING <span></span></div>
<h1 class="hero-title abs">Step into your<br>Digital Transformation</h1>
<p class="hero-text abs">Lorem ipsum dolor sit amet, consectetur adipiscing elit, sed d o eiusmod temp dipiscing elit, sed d</p>
<a class="btn hero-btn abs">Contact Us</a>

<h2 class="sec-title abs" style="top:840px">Why we are the best</h2>
<p class="sec-text abs" style="left:330px;top:894px">Lorem ipsum dolor sit amet, consectetur adipiscing elit, sed do eiusmod tempor incididunt ut labore et dolore magna aliqua. Ut enim ad min</p>

<div class="why-card abs" style="left:91px">
  <svg width="40" height="40" viewBox="0 0 40 40" fill="none" stroke="var(--lime)" stroke-width="2"><path d="M20 5l4 9 10 1-7 7 2 10-9-5-9 5 2-10-7-7 10-1z"/></svg>
  <h3>Personalized<br>Approach</h3><p>Lorem ipsum dolor sit amet,<br>consectetur adipiscing</p>
</div>
<div class="why-card featured abs" style="left:353px">
  <svg width="40" height="40" viewBox="0 0 40 40" fill="none" stroke="var(--lime)" stroke-width="2"><circle cx="18" cy="14" r="7"/><path d="M14 20l-4 12 8-4 8 4-4-12M6 36h28"/></svg>
  <h3>Proven<br>Track Record</h3><p>Lorem ipsum dolor sit amet,<br>consectetur adipiscing</p>
</div>
<div class="why-card abs" style="left:611px">
  <svg width="40" height="40" viewBox="0 0 40 40" fill="none" stroke="var(--lime)" stroke-width="2"><path d="M8 30a14 14 0 1 1 24 0"/><path d="M20 26l6-10"/><circle cx="20" cy="27" r="2"/></svg>
  <h3>Innovative<br>Solutions</h3><p>Lorem ipsum dolor sit amet,<br>consectetur adipiscing</p>
</div>
<div class="why-card abs" style="left:872px">
  <svg width="40" height="40" viewBox="0 0 40 40" fill="none" stroke="var(--lime)" stroke-width="2"><circle cx="20" cy="13" r="7"/><path d="M6 34c2-8 8-11 14-11s12 3 14 11z"/></svg>
  <h3>Client<br>Centric</h3><p>Lorem ipsum dolor sit amet,<br>consectetur adipiscing</p>
</div>
<a class="btn abs" style="left:523px;top:1225px;width:168px;height:43px;line-height:43px">Learn More</a>

<div class="vision-band abs"></div>
<div class="vision-photo abs" role="img" aria-label="Smiling businesswoman holding a tablet in a bright office"></div>
<h2 class="vision-title abs">Your Vision, Our Digital Mission</h2>
<p class="vision-text abs" style="top:1466px">Lorem ipsum dolor sit amet, consectetur adipiscing elit, sed do eiusmod tempor &nbsp;incididunt ut labore et dolore magna aliqua. Ut e nim ad min veniam, quis nostrud ex.</p>
<p class="vision-text abs" style="top:1541px">Lorem ipsum dolor sit amet, consectetur adipiscing elit, sed do eiusmod tempor &nbsp;incididunt ut labore et dolore magna aliqua. Ut e nim ad min veniam, quis nostrud ex. et dolore magna aliqua. Ut e nim ad min veniam, quis nostrud ex.</p>
<a class="btn vision-btn abs">Learn More <svg width="16" height="12" viewBox="0 0 16 12" fill="none" stroke="#fff" stroke-width="2"><path d="M0 6h14M9 1l5 5-5 5"/></svg></a>

<h2 class="sec-title abs" style="top:1908px">Our Services</h2>
<p class="sec-text abs" style="left:330px;top:1963px">Lorem ipsum dolor sit amet, consectetur adipiscing elit, sed do eiusmod tempor incididunt ut labore et dolore magna aliqua. Ut enim ad min</p>

<div class="svc-photo abs" style="left:93px;background:linear-gradient(135deg,#c9ced4,#6e7782 60%,#3c434c)" role="img" aria-label="Hand touching digital marketing interface icons"></div>
<div class="svc-photo abs" style="left:441px;background:linear-gradient(135deg,#e3e6e9,#8a8f96 50%,#3b3f45)" role="img" aria-label="Two colleagues reviewing work on a computer"></div>
<div class="svc-photo abs" style="left:788px;background:radial-gradient(circle at 50% 55%,#8fa6bf 0,#2f4763 40%,#142133 100%)" role="img" aria-label="Hands holding a glowing digital globe"></div>

<div class="svc-card abs" style="left:111px"><h3>Marketing Services</h3><p>Lorem ipsum dolor sit amet, cons ectetur adipiscing elit, sed do eiu smod tempor incididunt ut labore et dolore magna aliqua.</p><span class="more">LEARN MORE</span></div>
<div class="svc-card featured abs" style="left:459px"><h3>Online Booking Apps</h3><p>Lorem ipsum dolor sit amet, cons ectetur adipiscing elit, sed do eiu smod tempor incididunt ut labore et dolore magna aliqua.</p><span class="more">LEARN MORE</span></div>
<div class="svc-card abs" style="left:806px"><h3>Services Marketing</h3><p>Lorem ipsum dolor sit amet, cons ectetur adipiscing elit, sed do eiu smod tempor incididunt ut labore et dolore magna aliqua.</p><span class="more">LEARN MORE</span></div>

<div class="cta-band abs" role="img" aria-label="Dark blue digital network background"></div>
<div class="cta-phone abs">123-456-7890</div>
<h2 class="cta-title abs">Digital Excellence, Marketing Brilliance</h2>
<p class="sec-text abs" style="left:330px;top:2657px;color:#fff">Lorem ipsum dolor sit amet, consectetur adipiscing elit, sed do eiusmod tempor incididunt ut labore et dolore magna aliqua. Ut enim ad min</p>
<a class="cta-btn abs">Contact Us</a>

<h2 class="sec-title abs" style="top:2862px">Client Reviews</h2>
<p class="sec-text abs" style="left:330px;top:2919px">Lorem ipsum dolor sit amet, consectetur adipiscing elit, sed do eiusmod tempor incididunt ut labore et dolore magna aliqua. Ut enim ad min</p>

<div class="review abs" style="left:90px">
  <div class="rule"></div><div class="quote">&#8221;</div>
  <div class="stars">★★★★★</div>
  <p>Lorem ipsum dolor sit amet, consectetur adipiscing elit, sed do eiusmod tempor incididunt ut labore et d olore magna aliqua.</p>
  <h4>Nora Halvey</h4><div class="place">Green Valley</div>
  <div class="avatar" style="background:#c9b8a6" role="img" aria-label="Reviewer portrait"></div>
</div>
<div class="review abs" style="left:611px">
  <div class="rule"></div><div class="quote">&#8221;</div>
  <div class="stars">★★★★★</div>
  <p>Lorem ipsum dolor sit amet, consectetur adipiscing elit, sed do eiusmod tempor incididunt ut labore et d olore magna aliqua.</p>
  <h4>Nora Halvey</h4><div class="place">Green Valley</div>
  <div class="avatar" style="background:#d1a58e" role="img" aria-label="Reviewer portrait"></div>
</div>
<div class="dots abs"><span></span><span></span><span class="off"></span><span></span></div>

<h2 class="sec-title abs" style="top:3417px">Feel free to contact us</h2>
<p class="sec-text abs" style="left:330px;top:3474px">Lorem ipsum dolor sit amet, consectetur adipiscing elit, sed do eiusmod tempor incididunt ut labore et dolore magna aliqua. Ut enim ad min</p>

<div class="contact-box abs"></div>
<div class="contact-panel abs" role="img" aria-label="Customer support agent with headset, blue overlay"></div>
<div class="contact-info abs">
  <div class="label">CONTACT US</div>
  <div class="call">Call: 0123456789</div>
  <div class="small" style="margin-top:6px">info@company.com</div>
  <div class="small" style="margin-top:20px">Address:<br>SOME PLACE<br>51100 Road</div>
  <div class="small" style="margin-top:18px">Operating Hours<br>Monday to Saturday: 9:00 - 18:00<br>Sunday: Closed</div>
</div>
<div class="socials abs"><span></span><span class="on"></span><span></span><span></span></div>

<div class="form-title abs">FREE CONSULTATION</div>
<div class="field abs" style="top:3682px;height:32px">Your Name</div>
<div class="field abs" style="top:3731px;height:32px">Email</div>
<div class="field abs" style="top:3780px;height:32px">Phone</div>
<div class="field abs" style="top:3829px;height:94px">Message</div>
<a class="btn submit abs">SUBMIT</a>

<footer class="footer abs"></footer>
<div class="info-strip abs"></div>
<div class="info-item abs" style="left:106px">
  <svg width="52" height="48" viewBox="0 0 52 48" fill="none" stroke="#fff" stroke-width="2"><path d="M26 30s-9-10-9-16a9 9 0 0 1 18 0c0 6-9 16-9 16z"/><circle cx="26" cy="14" r="3"/><path d="M14 28L3 44h46L38 28"/></svg>
  <div><h4>Location</h4><p>123, City, Country</p></div>
</div>
<svg class="divider abs" style="left:410px" viewBox="0 0 28 104" fill="none" stroke="#fff" stroke-width="2"><path d="M2 0l22 52-22 52"/></svg>
<div class="info-item abs" style="left:474px">
  <svg width="30" height="52" viewBox="0 0 30 52" fill="none" stroke="#fff" stroke-width="2"><rect x="3" y="2" width="24" height="48" rx="4"/><path d="M3 40h24M3 9h24"/></svg>
  <div><h4>Telephone</h4><p>+123 456 78890</p></div>
</div>
<svg class="divider abs" style="left:767px" viewBox="0 0 28 104" fill="none" stroke="#fff" stroke-width="2"><path d="M2 0l22 52-22 52"/></svg>
<div class="info-item abs" style="left:821px">
  <svg width="48" height="48" viewBox="0 0 48 48" fill="none" stroke="#fff" stroke-width="2"><path d="M4 18l20 14 20-14v26H4z"/><path d="M10 22V4h28v18M16 12h16M16 18h16"/></svg>
  <div><h4>Email</h4><p>info@company.com</p></div>
</div>

<h4 class="foot-head abs" style="left:66px">About Company</h4>
<p class="foot-text abs" style="left:66px;top:4353px;width:330px">Lorem ipsum dolor sit amet, consectetur adipis cing elit, sed do eiusmod tempor incididunt ut labore et dolore magna aliqua.</p>
<a class="read-more abs" style="left:66px;top:4466px">Read More</a>

<h4 class="foot-head abs" style="left:433px">Useful Links</h4>
<div class="foot-links abs" style="left:433px;top:4350px"><a>About Us</a><a>Projects</a><a>Blog</a><a>Contact Us</a></div>
<div class="foot-links abs" style="left:610px;top:4350px"><a>Services</a><a>Shop</a><a>Privacy Policy</a><a>Help Desk</a></div>

<h4 class="foot-head abs" style="left:797px">Subscribe</h4>
<p class="abs" style="left:797px;top:4360px;width:340px;color:#fff;font-size:14px;line-height:24px">If you have any questions, Subscribe to our newsleeter to know more</p>
<div class="subscribe abs"><span class="ph">Email</span><span class="go"><svg style="position:absolute;left:26px;top:19px" width="12" height="18" viewBox="0 0 12 18" fill="none" stroke="#fff" stroke-width="2.5"><path d="M2 2l7 7-7 7"/></svg></span></div>

<div class="foot-line abs"></div>
<div class="foot-logo abs"><span class="brand">Tallomex</span></div>
<div class="foot-social abs" style="left:900px"><span></span></div>
<div class="foot-social abs" style="left:960px"><span></span></div>
<div class="foot-social abs" style="left:1020px"><span></span></div>
<div class="foot-social abs" style="left:1080px;border-right:1px solid #3a4049"><span></span></div>

</body>
</html>
```